Moravel Aesthetic Doctor

I require an elegant, luxurious looking business card for my aesthetic business. I am a doctor and that will set me aside from competitors. I am planning to provide home and spa based treatments to clients with high expectations. I have attached my logo.

```html
<!DOCTYPE html>
<html lang="en">
<head>
<meta charset="utf-8">
<title>Moravel Aesthetic Doctor – Business Card</title>
<link href="https://fonts.googleapis.com/css2?family=Cinzel:wght@400&family=Montserrat:wght@400;700&display=swap" rel="stylesheet">
<style>
  :root {
    --stage: #2c2c2e;
    --blue-deep: #0d74cf;
    --blue-mid: #2b93dc;
    --blue-light: #5cb6e6;
    --sky: #4fb3e6;
    --ink: #6d6e71;
    --ink-soft: #8a8b8e;
    --paper: #ffffff;
    --dot: #d9dde2;
  }
  * { box-sizing: border-box; margin: 0; padding: 0; }
  html, body { width: 1200px; height: 866px; overflow: hidden; }
  body {
    background: var(--stage);
    display: flex;
    align-items: center;
    justify-content: center;
    gap: 40px;
    font-family: "Montserrat", Arial, sans-serif;
  }
  .card {
    position: relative;
    width: 540px;
    height: 309px;
    border-radius: 2px;
    overflow: hidden;
    box-shadow: 0 10px 24px rgba(0,0,0,.45);
  }

  /* Front */
  .card-front { color: var(--paper); }
  .wave-field {
    position: absolute; inset: 0;
    background:
      radial-gradient(ellipse 70% 60% at 25% 80%, rgba(140,210,245,.45), transparent 70%),
      radial-gradient(ellipse 60% 50% at 80% 20%, rgba(120,200,240,.35), transparent 70%),
      linear-gradient(160deg, var(--blue-light) 0%, var(--blue-mid) 45%, var(--blue-deep) 100%);
  }
  .front-lockup {
    position: absolute; inset: 0;
    display: flex; flex-direction: column;
    align-items: center; justify-content: center;
    text-align: center;
  }
  .brand-name {
    font-family: "Cinzel", Georgia, serif;
    font-weight: 400;
    font-size: 52px;
    letter-spacing: 4px;
    line-height: 1;
  }
  .brand-tag {
    font-family: "Cinzel", Georgia, serif;
    font-weight: 400;
    font-size: 25px;
    letter-spacing: 2px;
    margin-top: 4px;
  }
  .brand-services {
    font-size: 11px;
    letter-spacing: 1px;
    margin-top: 12px;
  }

  /* Back */
  .card-back { background: var(--paper); }
  .back-lockup {
    position: absolute; top: 58px; right: 38px;
    display: flex; align-items: center; gap: 12px;
    color: var(--sky);
    font-family: "Cinzel", Georgia, serif;
    text-align: left;
  }
  .back-lockup .mark {
    width: 40px; height: 40px; border-radius: 50%;
    background: var(--sky);
  }
  .back-lockup .brand-name { font-size: 34px; letter-spacing: 3px; }
  .back-lockup .brand-tag { font-size: 15px; letter-spacing: 1.5px; margin-top: 2px; }

  .person {
    position: absolute; left: 38px; top: 140px;
  }
  .person-name {
    color: var(--ink);
    font-weight: 700;
    font-size: 17px;
  }
  .person-name .credentials {
    color: var(--sky);
    font-size: 10px;
    font-weight: 400;
    margin-left: 4px;
  }
  .person-title {
    color: var(--sky);
    font-size: 12px;
    margin-top: 2px;
  }
  .contact-list { list-style: none; margin-top: 12px; }
  .contact-list li {
    display: flex; align-items: center; gap: 8px;
    color: var(--ink-soft);
    font-size: 12px;
    line-height: 19px;
  }
  .contact-list svg { width: 12px; height: 12px; fill: none; stroke: var(--sky); stroke-width: 1.6; }

  .social-dots {
    position: absolute; right: 34px; bottom: 24px;
    display: flex; gap: 6px;
  }
  .social-dots span {
    width: 18px; height: 18px; border-radius: 50%;
    background: var(--dot);
  }
</style>
</head>
<body>
  <section class="card card-front">
    <div class="wave-field" role="img" aria-label="Flowing blue wave pattern background"></div>
    <div class="front-lockup">
      <div class="brand-name">MORAVEL</div>
      <div class="brand-tag">AESTHETIC DOCTOR</div>
      <div class="brand-services">HOME AND SPA BASED TREATMENTS</div>
    </div>
  </section>

  <section class="card card-back">
    <div class="back-lockup">
      <span class="mark"></span>
      <div>
        <div class="brand-name">MORAVEL</div>
        <div class="brand-tag">AESTHETIC DOCTOR</div>
      </div>
    </div>

    <div class="person">
      <div class="person-name">Dr Elise Varno<span class="credentials">MRCPCH MD</span></div>
      <div class="person-title">Australasian Diploma of Aesthetic Medicine</div>
      <ul class="contact-list">
        <li>
          <svg viewBox="0 0 12 12"><path d="M3 1.5 L4.6 3.4 L3.6 4.6 Q4.8 7 7.4 8.4 L8.6 7.4 L10.5 9 L9.3 10.6 Q4.5 10 1.4 3 Z"/></svg>
          0800 555 014
        </li>
        <li>
          <svg viewBox="0 0 12 12"><rect x="1" y="2.5" width="10" height="7"/><path d="M1 2.5 L6 6.5 L11 2.5"/></svg>
          elise@moravel.co.nz
        </li>
        <li>
          <svg viewBox="0 0 12 12"><circle cx="6" cy="6" r="4.8"/><ellipse cx="6" cy="6" rx="2" ry="4.8"/><path d="M1.2 6 H10.8"/></svg>
          www.moravel.co.nz
        </li>
      </ul>
    </div>

    <div class="social-dots"><span></span><span></span></div>
  </section>
</body>
</html>
```